Business Card Design

We would like to re-design our business cards. Our Company - Qwinrel Turbochargers, rebuilds turbochargers and sells replacement parts. Our website is: http://www.qwinrelturbochargers-example.com
We just had our logo changed. I will attach the file. Looking for fresh new/modern business card. We like the colors red, black, white and silver. Black background looks attractive, but not a requirement. The final design should communicate reasonable/competitive prices, top quality and reliability of our products.
Updates
Project Deadline Extended
Reason: Need to finalize the info on the card. Currently working on changing address and email info. Want to make sure it is the correct one before accepting the final design. Unless, this is something that can be changed at a later time..??
Industry/Entity Type
Business
Contact Information for Business Card
QWINREL TURBOCHARGERS, LLC
20473 Harwick Lane NE
Massillon, OH 44647
Tel: +1-555-214-7390
Fax: +1-555-267-1842
info@QwinrelTurbochargers-example.com
Our current business card had the following highlights:
*We rebuild all Turbocharges for Automotive, Diesel and Industrial
*Precision Balancing and in-house turbocharger needs
*All Turbocharger replacement parts are made in USA / U.K.
Look and feel
Each slider illustrates characteristics of the customer's brand and the style your logo design should communicate.

```html
<!DOCTYPE html>
<html lang="en">
<head>
<meta charset="utf-8">
<title>Qwinrel Turbochargers – Business Cards</title>
<link rel="stylesheet" href="https://fonts.googleapis.com/css2?family=Roboto+Condensed:wght@400;700&display=swap">
<style>
  :root {
    --bg: #d9d6d1;
    --card-white: #f7f7f7;
    --ink-black: #1d1d1f;
    --band-black: #232325;
    --brand-red: #e0272f;
    --text-grey: #2b2b2b;
    --white: #ffffff;
  }
  * { margin: 0; padding: 0; box-sizing: border-box; }
  html, body { width: 1200px; height: 902px; overflow: hidden; background: var(--bg); }
  body { position: relative; font-family: "Roboto Condensed", Arial, sans-serif; }

  .card {
    position: absolute;
    width: 660px; height: 377px;
    background: var(--card-white);
    overflow: hidden;
    box-shadow: 0 10px 28px rgba(0,0,0,0.22);
  }
  .card--front { left: 60px; top: 50px; }
  .card--back  { left: 480px; top: 470px; }
  .card__art { position: absolute; inset: 0; width: 100%; height: 100%; }

  .brand { position: absolute; display: flex; align-items: center; gap: 14px; }
  .brand__dot { width: 34px; height: 34px; border-radius: 50%; background: var(--brand-red); flex: none; }
  .brand__name {
    font-weight: 700; color: var(--ink-black);
    font-size: 38px; line-height: 0.95; letter-spacing: 0.5px;
  }
  .brand__name span { display: block; font-size: 26px; letter-spacing: 2px; }

  .card--front .brand { left: 300px; top: 140px; }
  .front__web {
    position: absolute; left: 348px; top: 246px;
    font-size: 19px; color: var(--text-grey);
  }

  .back__person { position: absolute; right: 42px; top: 30px; text-align: right; color: var(--white); }
  .back__name { font-size: 36px; font-weight: 400; line-height: 1; }
  .back__role { font-size: 14px; font-weight: 700; margin-top: 2px; }

  .card--back .brand { left: 250px; top: 160px; }

  .contacts { position: absolute; left: 44px; top: 248px; list-style: none; }
  .contacts li { display: flex; align-items: center; gap: 12px; font-size: 17px; color: var(--text-grey); height: 26px; }
  .contacts svg { width: 17px; height: 17px; flex: none; }
</style>
</head>
<body>

<section class="card card--front" aria-label="Business card front">
  <svg class="card__art" viewBox="0 0 660 377" preserveAspectRatio="none" aria-hidden="true">
    <path d="M0,0 H600 C420,18 210,150 120,377 H0 Z" fill="var(--band-black)"/>
    <path d="M560,16 C380,44 205,170 140,377 H158 C230,186 400,58 590,22 Z" fill="var(--brand-red)"/>
  </svg>
  <div class="brand">
    <div class="brand__dot"></div>
    <div class="brand__name">Qwinrel<span>Turbochargers</span></div>
  </div>
  <p class="front__web">www.qwinrelturbochargers-example.com</p>
</section>

<section class="card card--back" aria-label="Business card back">
  <svg class="card__art" viewBox="0 0 660 377" preserveAspectRatio="none" aria-hidden="true">
    <path d="M0,0 H660 V118 C470,92 240,110 0,200 Z" fill="var(--band-black)"/>
    <path d="M0,214 C240,124 470,104 660,132 V146 C470,120 250,138 0,222 Z" fill="var(--brand-red)"/>
  </svg>
  <div class="back__person">
    <p class="back__name">Employee name</p>
    <p class="back__role">Managing Director</p>
  </div>
  <div class="brand">
    <div class="brand__dot"></div>
    <div class="brand__name">Qwinrel<span>Turbochargers</span></div>
  </div>
  <ul class="contacts">
    <li>
      <svg viewBox="0 0 16 16" aria-hidden="true"><rect width="16" height="16" fill="var(--brand-red)"/><path d="M4.5,3.5 l2,0 l1,2.5 l-1.3,1 a6,6 0 0 0 2.8,2.8 l1,-1.3 l2.5,1 l0,2 a1,1 0 0 1 -1,1 a9,9 0 0 1 -8,-8 a1,1 0 0 1 1,-1 z" fill="var(--white)"/></svg>
      555-214-7390
    </li>
    <li>
      <svg viewBox="0 0 16 16" aria-hidden="true"><rect width="16" height="16" fill="var(--brand-red)"/><circle cx="8" cy="8" r="4.5" fill="none" stroke="var(--white)" stroke-width="1.3"/><path d="M3.5,8 H12.5 M8,3.5 C6,6 6,10 8,12.5 M8,3.5 C10,6 10,10 8,12.5" fill="none" stroke="var(--white)" stroke-width="1"/></svg>
      www.qwinrelturbochargers-example.com
    </li>
    <li>
      <svg viewBox="0 0 16 16" aria-hidden="true"><rect width="16" height="16" fill="var(--brand-red)"/><rect x="3" y="4.5" width="10" height="7" fill="none" stroke="var(--white)" stroke-width="1.2"/><path d="M3,4.5 L8,9 L13,4.5" fill="none" stroke="var(--white)" stroke-width="1.2"/></svg>
      info@QwinrelTurbochargers-example.com
    </li>
    <li>
      <svg viewBox="0 0 16 16" aria-hidden="true"><rect width="16" height="16" fill="var(--brand-red)"/><path d="M8,13 C5,9.5 4.5,8 4.5,6.5 a3.5,3.5 0 0 1 7,0 c0,1.5 -0.5,3 -3.5,6.5 z" fill="var(--white)"/><circle cx="8" cy="6.5" r="1.3" fill="var(--brand-red)"/></svg>
      5182 Harwick Lane NE North Ridgeport, Ohio
    </li>
  </ul>
</section>

</body>
</html>
```